Overnight youth camp for refugee kids needs a brochure in Arabic

We need a 3-fold "Z" brochure for an overnight youth camp for Arabic speaking teens in Canada from the Middle East and Africa. The camp's name is Camp Wrenfell. Design should have an outdoors, sports theme and be attractive to teens and their parents. We will supply pictures and text in English. All but the Camp Wrenfell name should be in Arabic.

```html
<!DOCTYPE html>
<html lang="ar" dir="rtl">
<head>
<meta charset="utf-8">
<title>Camp Wrenfell – Brochure</title>
<link rel="stylesheet" href="https://fonts.googleapis.com/css2?family=Cairo:wght@400;600;700;800&family=Lalezar&display=swap">
<style>
:root{
  --bg:#e4e4e4;
  --charcoal:#2a2a2a;
  --ink:#161616;
  --panel-dark:#1d1d1d;
  --white:#ffffff;
  --green:#7cc242;
  --green-dark:#5a9a2a;
  --teal:#56c3c6;
  --text:#222222;
  --muted:#cfcfcf;
}
*{box-sizing:border-box;margin:0;padding:0}
html,body{width:768px;height:1200px;overflow:hidden}
body{background:var(--bg);font-family:"Cairo",sans-serif;color:var(--text);position:relative}

.sheet{position:absolute;left:44px;width:680px;height:536px;background:var(--charcoal);overflow:hidden}
.sheet--outside{top:36px}
.sheet--inside{top:611px}

.panel{position:absolute;top:0;width:227px;height:536px;overflow:hidden}
.panel--left{left:0}
.panel--middle{left:227px;width:226px;background:var(--panel-dark)}
.panel--right{left:453px;background:var(--white)}

.footer-url{position:absolute;bottom:0;left:0;right:0;height:20px;background:var(--ink);color:var(--white);
  font-size:9px;font-weight:700;text-align:center;line-height:20px;direction:ltr}
.footer-url b{color:var(--green)}

.photo{position:absolute;background:linear-gradient(135deg,#5f8fb0,#c9a76a 60%,#4f7d3b)}
.photo--round{border-radius:50%;border:4px solid var(--green)}

.badge{position:absolute;border-radius:50%;background:var(--white);display:flex;align-items:center;justify-content:center;
  text-align:center;color:var(--green);font-weight:800;line-height:1;direction:ltr}

.wordmark{position:absolute;color:var(--green);font-weight:800;direction:ltr;text-align:center;line-height:1}

.body-text{position:absolute;font-size:7.4px;line-height:1.55;text-align:justify;font-weight:600}
.body-text--light{color:var(--white)}

.heading{position:absolute;font-weight:800;font-size:10px}
.heading em{font-style:normal;color:var(--green)}

.ticks{position:absolute;list-style:none;font-size:7px;font-weight:700;line-height:1.35}
.ticks li{position:relative;padding-right:13px;margin-bottom:4.5px}
.ticks li::before{content:"✓";position:absolute;right:0;top:0;width:8px;height:8px;border:1px solid var(--green);border-radius:50%;
  color:var(--green);font-size:6px;line-height:7px;text-align:center}

.register{position:absolute;left:14px;right:14px;color:var(--white);font-size:6.6px;line-height:1.5;font-weight:600;text-align:right}
.register .dates{color:var(--green);font-weight:800;float:left;direction:ltr;font-size:8px}
.register .dates b{color:var(--white)}

.pill{position:absolute;left:24px;right:24px;height:18px;border-radius:9px;background:var(--green);color:var(--ink);
  font-size:10px;font-weight:800;text-align:center;line-height:18px;direction:ltr}

.contact{position:absolute;left:54px;direction:ltr;color:var(--white);font-size:6.6px;line-height:1.3;text-align:left}
.contact li{list-style:none;display:flex;align-items:flex-start;gap:5px;margin-bottom:7px}
.contact svg{flex:none;width:8px;height:8px;fill:var(--muted)}

.title{position:absolute;font-family:"Lalezar",sans-serif;color:var(--ink);-webkit-text-stroke:0;text-shadow:0 0 0 #000;
  background:rgba(255,255,255,.85);padding:0 8px;border-radius:4px;line-height:1.2}

.ages{position:absolute;left:0;right:0;text-align:center;font-family:"Lalezar",sans-serif;font-size:17px;color:var(--ink)}
.ages em{font-style:normal;color:var(--green)}

svg.curve{position:absolute;left:0;width:100%}
</style>
</head>
<body>

<!-- OUTSIDE SPREAD -->
<section class="sheet sheet--outside">

  <div class="panel panel--left">
    <div class="photo" style="left:0;top:0;width:227px;height:200px;background:linear-gradient(160deg,#e8e8e8,#3d7fb0 45%,#f0c23a 70%,#2a6a9a)" role="img" aria-label="Children in life jackets riding on a boat"></div>
    <svg class="curve" style="top:130px;height:100px" viewBox="0 0 227 100" preserveAspectRatio="none" aria-hidden="true">
      <path d="M0 70 Q110 20 227 0 L227 100 L0 100Z" fill="#ffffff"/>
      <path d="M0 62 Q110 12 227 -8 L227 0 Q110 20 0 70Z" fill="#7cc242"/>
    </svg>
    <div class="photo photo--round" style="left:4px;top:140px;width:106px;height:106px;background:linear-gradient(150deg,#7fb6d8,#f2c230 55%,#2e6f9a)" role="img" aria-label="Child in a life jacket on a jet ski"></div>
    <div style="position:absolute;top:230px;left:0;right:0;bottom:0;background:var(--white)"></div>
    <p class="body-text" style="top:262px;left:20px;right:14px;color:var(--text)">القيم الصحية هي اساس فعالياتنا ومغامراتنا كل يوم في هذا المخيم. نحن حريصين على تزويد كل المشتركين والمشتركات بهذا المخيم بالذكريات والتعاليم التي لم ينسوها طوال حياتهم، بالإضافة الى الصداقات التي سوف تبدأ هنا وتستمر معهم حتى بعد مغادرتهم المخيم.</p>
    <p class="heading" style="top:330px;right:14px;font-size:9.5px">برنامجنا يتضمن كل من <em>الفعاليات</em> الاتية:</p>
    <ul class="ticks" style="top:352px;right:14px;left:14px">
      <li>السباحة</li><li>العاب الميدان</li><li>الحرف الفنية</li><li>القوارب والتجديف</li><li>التسلق</li><li>التجمع حول شعلة النار ليلاً</li><li>مهارات العيش في الطبيعة والهواء الطلق</li>
    </ul>
    <svg class="curve" style="top:440px;height:80px" viewBox="0 0 227 80" preserveAspectRatio="none" aria-hidden="true">
      <path d="M0 40 Q120 10 227 50 L227 80 L0 80Z" fill="#2a2a2a"/>
    </svg>
    <div class="wordmark" style="left:20px;top:468px;font-size:20px;width:140px;text-align:left">Camp Wrenfell</div>
    <div class="footer-url">www.camp<b>wrenfell</b>.ca</div>
  </div>

  <div class="panel panel--middle">
    <div class="badge" style="left:63px;top:10px;width:100px;height:100px;border:4px solid var(--charcoal);box-shadow:0 0 0 3px var(--white);font-size:15px">Camp<br>Wrenfell</div>
    <p class="body-text body-text--light" style="top:142px;left:14px;right:14px;font-size:8px">المخيم يقع بالقرب من مدينة ترينتون، اونتاريو على بعد ساعتين من مدينة تورنتو و ساعات من مدينة اوتاوا و ساعات من مدينة لندن.</p>
    <p class="body-text body-text--light" style="top:210px;left:14px;right:14px;font-size:8px">نحن حريصين على توفير كابينات نوم نظيفة ومريحة، قاعة طعام جديدة، صالة العاب رياضية، ملاعب رياضية، و ساحل مشرف على البحيرة الخاصة بالمخيم.</p>
    <div class="photo photo--round" style="left:58px;top:300px;width:110px;height:110px;background:linear-gradient(160deg,#9cc6e8,#6aa048 60%,#c9433a)" role="img" aria-label="Camp leader with two boys on a grassy field"></div>
    <p class="register" style="top:440px"><span class="dates"><b>2020</b> 23-28</span>للراغبين في التسجيل في المخيم في الفترة خلال، يرجى زيارتنا على الموقع الالكتروني الاتي:</p>
    <div class="pill" style="top:466px">www.campwrenfell.ca</div>
    <ul class="contact" style="top:494px">
      <li><svg viewBox="0 0 10 10"><path d="M5 0a3.5 3.5 0 0 0-3.5 3.5C1.5 6 5 10 5 10s3.5-4 3.5-6.5A3.5 3.5 0 0 0 5 0zm0 5a1.5 1.5 0 1 1 0-3 1.5 1.5 0 0 1 0 3z"/></svg><span>48 Larchmere Lane, Ottawa,<br>Ontario K0A 1B0</span></li>
      <li><svg viewBox="0 0 10 10"><path d="M0 2h10v6H0z M0 2l5 3.5L10 2" stroke="#1d1d1d" stroke-width=".6"/></svg><span>info@campwrenfell.ca</span></li>
      <li><svg viewBox="0 0 10 10"><path d="M2 0l2 2.5-1 1.2a6 6 0 0 0 3.3 3.3l1.2-1L10 8l-1.5 2C4 10 0 6 0 1.5z"/></svg><span>(555) 010-0147</span></li>
    </ul>
    <div class="footer-url">www.camp<b>wrenfell</b>.ca</div>
  </div>

  <div class="panel panel--right">
    <svg class="curve" style="top:0;height:160px" viewBox="0 0 227 160" preserveAspectRatio="none" aria-hidden="true">
      <path d="M0 0 L227 0 L227 8 Q120 70 0 60Z" fill="#2a2a2a"/>
      <path d="M0 60 Q120 70 227 8 L227 18 Q120 80 0 66Z" fill="#7cc242"/>
    </svg>
    <div class="badge" style="left:78px;top:12px;width:124px;height:124px;border:4px solid var(--charcoal);font-size:19px">Camp<br>Wrenfell</div>
    <div class="photo" style="left:0;top:152px;width:227px;height:240px;background:linear-gradient(150deg,#6a8a4e,#d86b8a 40%,#3a6fc0 65%,#9a7a55)" role="img" aria-label="Group of smiling children and camp leaders cheering outdoors"></div>
    <div class="title" style="top:208px;left:46px;font-size:24px">مرحبا بفصل</div>
    <div class="title" style="top:328px;left:10px;font-size:34px">الصيف الرائع</div>
    <svg class="curve" style="top:370px;height:36px" viewBox="0 0 227 36" preserveAspectRatio="none" aria-hidden="true">
      <path d="M0 36 L0 20 Q120 30 227 0 L227 36Z" fill="#ffffff"/>
      <path d="M0 14 Q120 24 227 -6 L227 0 Q120 30 0 20Z" fill="#7cc242"/>
    </svg>
    <p class="body-text" style="top:410px;left:14px;right:14px;text-align:center;font-size:8.2px;font-weight:700">مغامرات ترفيهية في الهواء الطلق والطبيعة الخلابة تتضمن السباحة و قوارب التجديف وماغيرها من فعاليات اخرى مخيم صيفي للاولاد والبنات للاعمار</p>
    <p class="ages" style="top:470px"><em>9</em> سنوات الى <em>16</em> سنة</p>
    <div class="footer-url">www.camp<b>wrenfell</b>.ca</div>
  </div>
</section>

<!-- INSIDE SPREAD -->
<section class="sheet sheet--inside">

  <div class="photo" style="left:0;top:0;width:453px;height:270px;background:linear-gradient(140deg,#c9b28a,#4a3a30 35%,#b8b0a4 60%,#3a3a3a)" role="img" aria-label="Campers gathered around a dining table sharing a meal"></div>

  <div class="panel panel--left" style="top:0;background:transparent">
    <svg class="curve" style="top:180px;height:120px" viewBox="0 0 227 120" preserveAspectRatio="none" aria-hidden="true">
      <path d="M0 40 Q130 90 227 60 L227 120 L0 120Z" fill="#ffffff"/>
      <path d="M0 32 Q130 82 227 52 L227 60 Q130 90 0 40Z" fill="#7cc242"/>
    </svg>
    <div class="photo photo--round" style="left:4px;top:150px;width:120px;height:120px;background:linear-gradient(150deg,#d9d2c4,#c8745a 50%,#3c6f9a)" role="img" aria-label="Group of younger campers sitting together indoors"></div>
    <div class="photo photo--round" style="left:120px;top:172px;width:96px;height:96px;background:linear-gradient(150deg,#e8e4dc,#c58a4a 55%,#7a5a3a)" role="img" aria-label="Trays of freshly baked pizza in the kitchen"></div>
    <div style="position:absolute;top:290px;left:0;right:0;bottom:0;background:var(--white)"></div>
    <p class="body-text" style="top:292px;left:14px;right:14px">سوف نقوم بتوفير وجبات طعام صحية (حلال) خالية من لحم الخنزير و منتجاته. عادة يتم تقديم الحبوب والفطائر و التوست الفرنسي على الفطور، و تقديم السندويشات والحساء مع الفواكه على الغداء، و تقديم السباكيتي والهمبركر والنقانق على العشاء.</p>
    <p class="heading" style="top:348px;right:14px;left:10px;font-size:10px;line-height:1.4">التكلفة: <em style="font-size:13px">$100</em> لكل استمارة لكل مشترك و تشمل كل ما يلي:</p>
    <ul class="ticks" style="top:390px;right:14px;left:14px">
      <li>توفير وجبات الطعام والوجبات الخفيفة</li><li>طهي الطعام والشاوي</li><li>توفير المعدات الرياضية واستعمال البحيرة</li><li>توفير اللوازم الحرفية والفنية</li><li>تزويد كل مشترك بصور المخيم على قرص مخزن</li><li>تزويد كل مشترك بصورة جماعية لكل المشتركين</li>
    </ul>
    <svg class="curve" style="top:452px;height:70px" viewBox="0 0 227 70" preserveAspectRatio="none" aria-hidden="true">
      <path d="M0 36 Q120 6 227 40 L227 70 L0 70Z" fill="#2a2a2a"/>
    </svg>
    <div class="wordmark" style="left:20px;top:480px;font-size:20px;width:140px;text-align:left">Camp Wrenfell</div>
    <div class="footer-url">www.camp<b>wrenfell</b>.ca</div>
  </div>

  <div class="panel panel--middle" style="background:transparent">
    <div style="position:absolute;top:270px;left:0;right:0;bottom:0;background:var(--panel-dark)"></div>
    <div class="badge" style="left:54px;top:188px;width:118px;height:118px;border:4px solid var(--charcoal);box-shadow:0 0 0 3px var(--white);font-size:17px">Camp<br>Wrenfell</div>
    <p class="body-text body-text--light" style="top:312px;left:12px;right:12px;font-size:8.6px;line-height:1.5">مخيم مع المبيت لمدة خمسة ليالي مخصص للشباب من دول شمال افريقيا والشرق الوسط. الهدف الرئيسي من من المخيم هو التركيز على تطوير الشباب و تحفيزهم على ان يكونوا قادة المستقبل عن طريق ادخال تعاليم الله في حياة المشتركين. املناهو ان يغادر كل مشترك او مشتركة هذا المخيم مع ذكريات رائعة سوف يتذكرونها طوال حياتهم والمزيد من الثقة بالنفس والتأكيد على قيمة الذات و احترام اكبر للاخرين وانفسهم و مخلوقات الله وقدرة اكبر على اقامة صداقات جديدة والحفاظ عليها وفهم اعمق لوجود الله في حياتهم.</p>
    <p class="register" style="top:478px"><span class="dates"><b>2020</b> 23-28</span>للراغبين في التسجيل في المخيم في الفترة خلال، يرجى زيارتنا على الموقع الالكتروني الاتي:</p>
    <div class="pill" style="top:500px;height:16px;line-height:16px">www.campwrenfell.ca</div>
    <div class="footer-url">www.camp<b>wrenfell</b>.ca</div>
  </div>

  <div class="panel panel--right">
    <p class="heading" style="top:36px;right:18px;left:14px;font-size:12px;line-height:1.35">نحن ملتزمون لتحقيق الاهداف التالية:</p>
    <ul class="ticks" style="top:88px;right:14px;left:12px;font-size:6.8px;font-weight:600;line-height:1.6">
      <li style="margin-bottom:12px">الحرص على حصول جميع المشتركين في المخيم على الراحة التامة من خلال توفير الاماكن المخصصة للاقامة، واختيار الاشخاص الذين سوف يقيموا معهم في غرفهم، وتوفير البرامج الترفيهية والاشخاص المشرفين عليهم.</li>
      <li style="margin-bottom:12px">الحرص على التواصل مع كل مشترك و مساعدة كل الاولاد والبنات على التواصل فيما بينهم والبيئة المحيطة بهم.</li>
      <li style="margin-bottom:12px">الحرص على ان المشرفين على المخيم ان يكونوا مدركين ان كل مشترك او مشتركة هو الهدف الرئيسي من المخيم وهم يستحقون منا كل الرعاية، والعناية و الاهتمام اينما كانوا ليلا او نهارا.</li>
      <li>الحرص على ان يكون المخيم تجربة ممتعة وخبرة ذات مغزى لكل المشتركين.</li>
    </ul>
    <div class="photo" style="left:0;top:380px;width:227px;height:136px;background:linear-gradient(180deg,#8fb6d8,#b9c9d6 35%,#6c8a4c 60%,#5a4a3a)" role="img" aria-label="Campers seated around an evening campfire outside a barn"></div>
    <svg class="curve" style="top:350px;height:50px" viewBox="0 0 227 50" preserveAspectRatio="none" aria-hidden="true">
      <path d="M0 0 L227 0 L227 20 Q110 50 0 30Z" fill="#ffffff"/>
      <path d="M0 30 Q110 50 227 20 L227 26 Q110 56 0 36Z" fill="#7cc242"/>
    </svg>
    <div class="photo photo--round" style="left:16px;top:300px;width:104px;height:104px;background:linear-gradient(150deg,#cfd8c4,#3a3a3a 45%,#8a6a4a)" role="img" aria-label="Camper practising archery"></div>
    <div class="footer-url">www.camp<b>wrenfell</b>.ca</div>
  </div>
</section>

</body>
</html>
```